Business Card Design

Looking for business card designs for a new business. there will be two cards of the same design (both lots of information below in contact info). We would like the logo diagonally across the card with the information split above and below the logo similar to sketch. happy to look at similar alternatives
Please use same colours as in logo design

Industry/Entity Type

Business

Contact Information for Business Card

Dwight Halloran
mob - 0491 738 204
ph - 02 6148 3920
fax - 02 6148 3975
email - dwight@kestrelbeams.com.au
14 Larkmoor Road, Taminda NSW 2340

Colin Marchetti
mob - 0438 912 557
ph - 02 6148 3920
fax - 02 6148 3975
email - colin@kestrelbeams.com.au

```html
<!DOCTYPE html>
<html lang="en">
<head>
<meta charset="utf-8">
<title>Kestrel Beams – Business Cards</title>
<link href="https://fonts.googleapis.com/css2?family=Open+Sans:wght@400;600;700;800&display=swap" rel="stylesheet">
<style>
  :root {
    --teal: #137b78;
    --ink: #111111;
    --paper: #ffffff;
    --backdrop: #e9e9e7;
    --url-grey: #3a3a3a;
  }
  * { box-sizing: border-box; margin: 0; padding: 0; }
  html, body {
    width: 1200px;
    height: 772px;
    overflow: hidden;
    background: var(--backdrop);
    font-family: "Open Sans", Arial, sans-serif;
  }
  .stage { position: relative; width: 1200px; height: 772px; }

  /* ---------- Front card ---------- */
  .card-front {
    position: absolute;
    left: 34px; top: 196px;
    width: 701px; height: 401px;
    background: var(--paper);
    overflow: hidden;
    box-shadow: 0 2px 6px rgba(0,0,0,.18);
  }
  .card-front .bands {
    position: absolute; inset: 0;
    width: 100%; height: 100%;
  }
  .holder {
    position: absolute;
    left: 36px; top: 40px;
    color: var(--paper);
  }
  .holder .name {
    font-weight: 700;
    font-size: 20px;
    letter-spacing: .2px;
  }
  .holder .mobile {
    margin-top: 30px;
    font-size: 16.5px;
    display: flex; align-items: center; gap: 6px;
  }
  .icon { width: 14px; height: 14px; flex: none; }

  .wordmark-front {
    position: absolute;
    left: 345px; top: 192px;
    transform: translate(-50%, -50%) rotate(-25deg);
    display: flex; align-items: center; gap: 12px;
    white-space: nowrap;
  }
  .wordmark-front .mark {
    width: 30px; height: 30px;
    background: var(--teal);
  }
  .wordmark-front .brand {
    font-weight: 800;
    font-size: 50px;
    color: var(--ink);
    letter-spacing: -.5px;
  }

  .contact {
    position: absolute;
    right: 18px; bottom: 11px;
    text-align: right;
    font-size: 16.5px;
    line-height: 1;
  }
  .contact li {
    list-style: none;
    display: flex; justify-content: flex-end; align-items: center; gap: 6px;
    color: var(--paper);
    margin-bottom: 10px;
  }
  .contact li.address {
    color: var(--ink);
    margin-top: 18px;
    margin-bottom: 0;
  }

  /* ---------- Back card ---------- */
  .card-back {
    position: absolute;
    left: 778px; top: 41px;
    width: 403px; height: 703px;
    background: var(--paper);
    border: 1.5px solid var(--ink);
    box-shadow: 0 2px 6px rgba(0,0,0,.18);
    overflow: hidden;
  }
  .back-url {
    position: absolute;
    left: 66px; top: 50%;
    transform: translate(-50%, -50%) rotate(90deg);
    font-size: 18px;
    letter-spacing: 4.6px;
    color: var(--url-grey);
    white-space: nowrap;
  }
  .wordmark-back {
    position: absolute;
    left: 200px; top: 50%;
    transform: translate(-50%, -50%) rotate(90deg);
    display: flex; align-items: center; gap: 16px;
    white-space: nowrap;
  }
  .wordmark-back .mark {
    width: 38px; height: 38px;
    background: var(--teal);
  }
  .wordmark-back .brand {
    font-weight: 800;
    font-size: 64px;
    color: var(--ink);
    letter-spacing: -.5px;
  }
</style>
</head>
<body>
<main class="stage">

  <section class="card-front" aria-label="Business card front">
    <svg class="bands" viewBox="0 0 508 291" preserveAspectRatio="none" aria-hidden="true">
      <polygon points="0,0 340,0 0,160" fill="var(--ink)"/>
      <line x1="372" y1="0" x2="0" y2="176" stroke="var(--teal)" stroke-width="2.4"/>
      <polygon points="508,128 508,291 170,291" fill="var(--teal)"/>
      <line x1="508" y1="118" x2="156" y2="291" stroke="var(--ink)" stroke-width="2"/>
    </svg>

    <div class="holder">
      <p class="name">Colin Marchetti</p>
      <p class="mobile">
        <svg class="icon" viewBox="0 0 14 14" aria-hidden="true"><rect x="4" y="1" width="6" height="12" rx="1.2" fill="none" stroke="currentColor" stroke-width="1.4"/><circle cx="7" cy="10.8" r=".8" fill="currentColor"/></svg>
        0438 912 557
      </p>
    </div>

    <div class="wordmark-front">
      <span class="mark" aria-hidden="true"></span>
      <span class="brand">Kestrel Beams</span>
    </div>

    <ul class="contact">
      <li>
        <svg class="icon" viewBox="0 0 14 14" aria-hidden="true"><path d="M3 1.5 L5.2 4 L4 5.6 C4.8 7.4 6.6 9.2 8.4 10 L10 8.8 L12.5 11 L11 12.6 C6.5 12.4 1.6 7.5 1.4 3 Z" fill="currentColor"/></svg>
        02 6148 3920
      </li>
      <li>
        <svg class="icon" viewBox="0 0 14 14" aria-hidden="true"><rect x="3.5" y="1.5" width="7" height="4" fill="none" stroke="currentColor" stroke-width="1.2"/><rect x="1" y="5.5" width="12" height="6" rx="1" fill="currentColor"/><rect x="3.5" y="9" width="7" height="3.5" fill="var(--paper)" stroke="currentColor" stroke-width="1"/></svg>
        02 6148 3975
      </li>
      <li>
        <svg class="icon" viewBox="0 0 14 14" aria-hidden="true"><rect x="1" y="3" width="12" height="8.5" rx="1" fill="currentColor"/><path d="M1.5 3.6 L7 8 L12.5 3.6" fill="none" stroke="var(--teal)" stroke-width="1.2"/></svg>
        colin@kestrelbeams.com.au
      </li>
      <li class="address">14 Larkmoor Road, Brackenvale NSW 2391</li>
    </ul>
  </section>

  <section class="card-back" aria-label="Business card back">
    <p class="back-url">www.kestrelbeams.com.au</p>
    <div class="wordmark-back">
      <span class="mark" aria-hidden="true"></span>
      <span class="brand">Kestrel Beams</span>
    </div>
  </section>

</main>
</body>
</html>
```